I have a business that exists already (Linden Conservatory of Music) that we offer music lessons to all instruments. I recently opened a smaller version called CHORDS by Linden that will only teach piano lessons. What I'm looking for now is a 3 page Website on word press. After I choose the design I like I want to be able to take over the website and bring it to our hosting company. We want full control of it and our team will take over. The reason I'm doing this is to have other visions and ideas from others. The first page will be about the company and our message/vision. Second page about the piano lessons. The third will be about franchising this concept "Chords by Linden" Attached are 3 Logos . Please refer to our existing website www.lindenmusicconservatory.example to look at our piano page and franchising page. Please feel free to message me if you need more info. Thanks
Please note I do not want the new website (Chords by Linden) To look like the other Website (Linden Conservatory of Music) Fresh new look. I do not want the colours red or using the Red logo. I only provided it so that you have an Idea of What the other business looks like and that you can take the piano content and franchise content off of it. Chords by Linden is smaller concept and only piano lessons.
Thanks
Only Piano lessons for all students
3 page

```html
<!DOCTYPE html>
<html lang="en">
<head>
<meta charset="utf-8">
<title>Chords by Linden</title>
<link rel="stylesheet" href="https://fonts.googleapis.com/css2?family=Cinzel:wght@400;600&family=Great+Vibes&family=Open+Sans:wght@400;600;700&family=Lora:ital@0;1&display=swap">
<style>
:root{
  --gold:#d9a93a;
  --blue:#2f8fd8;
  --teal:#4fc3b8;
  --ink:#2b2b2b;
  --muted:#6d6d6d;
  --dark:#111111;
  --band:#3a3a3a;
  --line:#e2e2e2;
  --white:#ffffff;
}
*{box-sizing:border-box;margin:0;padding:0}
html,body{width:1200px;height:2812px;overflow:hidden}
body{font-family:"Open Sans",Arial,sans-serif;color:var(--ink);background:var(--white);position:relative}
.serif{font-family:"Cinzel",Georgia,serif}
.script{font-family:"Great Vibes",cursive}
.btn{display:inline-block;font-size:14px;font-weight:600;letter-spacing:1px;text-transform:uppercase;padding:10px 26px;color:var(--white);border-radius:2px}

/* hero */
.hero{position:absolute;left:0;top:0;width:1200px;height:600px;overflow:hidden;
  background:linear-gradient(90deg,#0c0c0e 0%,#17161a 40%,#2a2018 60%,#5a3e1f 80%,#8a6330 100%)}
.hero-photo{position:absolute;left:560px;top:0;width:640px;height:600px;
  background:radial-gradient(ellipse at 55% 40%,rgba(226,176,98,.55),rgba(80,52,28,.35) 55%,rgba(12,12,14,0) 85%)}
.topbar{position:absolute;left:0;top:0;width:1200px;height:84px;background:rgba(0,0,0,.55);display:flex;align-items:center;padding:0 40px}
.brand{display:flex;align-items:center;gap:10px;color:var(--white);font-family:"Cinzel",Georgia,serif;font-size:22px;font-weight:600;width:420px}
.brand-dot{width:12px;height:12px;border-radius:50%;background:var(--gold)}
.nav{display:flex;list-style:none;gap:6px;margin-left:0}
.nav li{font-size:13px;font-weight:600;color:var(--white);letter-spacing:1px;padding:8px 18px}
.nav li.active{background:var(--gold);color:var(--dark)}
.social{display:flex;gap:10px;margin-left:30px}
.social span{width:22px;height:22px;background:rgba(255,255,255,.2);border-radius:2px}
.hero-copy{position:absolute;left:150px;top:225px;color:var(--white)}
.hero-copy .script{font-size:62px;color:var(--gold);line-height:1}
.hero-copy h1{font-family:"Cinzel",Georgia,serif;font-weight:400;font-size:56px;letter-spacing:2px;margin:6px 0 28px}
.hero-copy .btn{background:var(--gold);color:var(--dark)}

/* about */
.about{position:absolute;top:600px;left:0;width:1200px;height:400px}
.about-title{position:absolute;top:24px;width:1200px;text-align:center;font-size:40px}
.about-title .serif{color:var(--blue)}
.about-title .serif b{color:var(--ink);font-weight:600}
.about-title .script{font-size:28px;color:var(--ink)}
.about-rule{position:absolute;top:86px;left:470px;width:260px;height:2px;background:var(--blue)}
.about-lead{position:absolute;top:102px;left:190px;width:820px;font-size:14px;line-height:22px;color:var(--muted);text-align:center}
.collage-back{position:absolute;left:240px;top:190px;width:260px;height:200px;background:linear-gradient(135deg,#d6d6d6,#9a9a9a)}
.collage-front{position:absolute;left:140px;top:152px;width:260px;height:200px;background:linear-gradient(135deg,#6a4a32,#c79a6b 60%,#ead0ad);border:6px solid var(--white);box-shadow:0 4px 12px rgba(0,0,0,.2)}
.playing{position:absolute;left:590px;top:160px;width:480px}
.playing h2{font-family:"Great Vibes",cursive;font-weight:400;color:var(--blue);font-size:44px;line-height:1;margin-bottom:12px}
.playing p{font-size:13px;line-height:21px;color:var(--muted);margin-bottom:10px}
.playing .btn{background:var(--blue);margin-left:140px}

/* vision */
.vision{position:absolute;top:1020px;left:0;width:1200px;height:360px;
  background:linear-gradient(160deg,#262626 0%,#4b4b4b 45%,#6d6d6d 70%,#2f2f2f 100%);text-align:center;color:var(--white)}
.vision h2{font-family:"Cinzel",Georgia,serif;font-weight:400;font-size:38px;letter-spacing:2px;padding-top:70px}
.vision-rule{width:120px;height:2px;background:var(--white);margin:10px auto 18px}
.vision p{width:760px;margin:0 auto 22px;font-size:14px;line-height:22px;color:#e8e8e8}
.vision .btn{background:var(--blue)}

/* programs */
.programs{position:absolute;top:1420px;left:0;width:1200px;height:560px}
.programs h2{position:absolute;left:140px;top:16px;border-left:5px solid var(--blue);padding-left:14px;font-size:22px;font-weight:700;line-height:30px;color:var(--ink);text-transform:uppercase;width:560px}
.programs-photo{position:absolute;left:140px;top:96px;width:360px;height:420px;border:10px solid var(--blue);background:linear-gradient(140deg,#f2f2f2,#cfcfcf 50%,#6b5a4e)}
.program-grid{position:absolute;left:520px;top:96px;width:540px;display:grid;grid-template-columns:1fr 1fr;gap:22px}
.program-item{height:124px;border:1px solid var(--line);border-left:4px solid var(--blue);padding:16px 18px;font-size:14px;line-height:22px;color:var(--muted);box-shadow:0 2px 8px rgba(0,0,0,.06)}

/* quote */
.quote{position:absolute;top:2120px;left:320px;width:560px;height:200px;background:var(--white);box-shadow:0 4px 24px rgba(0,0,0,.12);text-align:center;padding-top:50px}
.quote p{font-family:"Lora",Georgia,serif;font-style:italic;font-size:20px;line-height:30px;color:var(--ink);width:440px;margin:0 auto}
.quote .q-rule{width:200px;height:1px;background:var(--line);margin:16px auto 10px}
.quote cite{font-style:normal;font-size:14px;font-weight:600;letter-spacing:1px;color:var(--blue)}

/* franchise */
.franchise{position:absolute;top:2380px;left:0;width:1200px;text-align:center}
.franchise h2{font-family:"Lora",Georgia,serif;font-weight:400;font-size:42px;color:var(--ink)}
.franchise h3{font-family:"Lora",Georgia,serif;font-weight:400;font-size:18px;letter-spacing:1px;color:var(--ink);margin:6px 0 20px}
.franchise .btn{background:var(--teal);font-size:13px;padding:8px 26px}

/* footer */
.footer{position:absolute;top:2608px;left:0;width:1200px;height:160px;background:var(--dark);color:var(--white);display:flex;align-items:center;padding:0 180px;gap:0}
.contact{display:flex;align-items:center;gap:14px;width:260px}
.contact-icon{width:40px;height:40px;border:2px solid var(--white);border-radius:50%;display:flex;align-items:center;justify-content:center}
.contact small{display:block;font-size:12px;color:#bbbbbb}
.contact strong{font-size:15px;font-weight:600}
.footer-brand{width:280px;padding-left:20px}
.footer-brand strong{font-family:"Cinzel",Georgia,serif;font-size:18px;font-weight:600}
.footer-brand small{display:block;font-size:12px;color:#bbbbbb;line-height:18px;margin-top:4px}
.footer-social{display:flex;gap:8px;margin-left:auto}
.footer-social span{width:26px;height:26px;background:#444;border-radius:2px}
.legal{position:absolute;top:2768px;left:0;width:1200px;height:44px;background:var(--teal);color:var(--white);font-size:12px;line-height:44px;padding-left:140px}
</style>
</head>
<body>

<header class="hero">
  <div class="hero-photo" role="img" aria-label="Young pianist playing a grand piano in warm stage light"></div>
  <nav class="topbar">
    <div class="brand"><span class="brand-dot"></span>Chords by Linden</div>
    <ul class="nav">
      <li class="active">HOME</li>
      <li>PIANO LESSONS</li>
      <li>FRANCHISING</li>
      <li>CONTACT US</li>
    </ul>
    <div class="social"><span></span><span></span><span></span><span></span></div>
  </nav>
  <div class="hero-copy">
    <div class="script">Welcome to</div>
    <h1>CHORDS BY LINDEN</h1>
    <span class="btn">Read More</span>
  </div>
</header>

<section class="about">
  <div class="about-title"><span class="serif">ABOUT <b>CHORDS</b></span> <span class="script">by Linden</span></div>
  <div class="about-rule"></div>
  <p class="about-lead">Chords by Linden is a dedicated piano studio where students of every age build skill, confidence and a lifelong love of music. Our teachers guide each learner with patient, personal lessons in a warm and welcoming space.</p>
  <div class="collage-back" role="img" aria-label="Grand piano in a bright lesson room"></div>
  <div class="collage-front" role="img" aria-label="Teacher guiding a student at the piano"></div>
  <div class="playing">
    <h2>Playing the Piano</h2>
    <p>When you think of a piano, you probably envision black and white keys but the piano is more than those harmonious sounds created by the player. The versatility and the musicianship instilled into the player from these keys is the true magic that comes from playing piano!</p>
    <p>Starting from the grassroots, experience different methods and styles of playing piano.</p>
    <span class="btn">Read More</span>
  </div>
</section>

<section class="vision" role="img" aria-label="Close view of piano keys in soft grey light">
  <h2>OUR VISION</h2>
  <div class="vision-rule"></div>
  <p>Our mission is to give every student a joyful start at the piano and the steady guidance to grow. We blend classic technique with modern repertoire so each lesson feels fresh, focused and rewarding.</p>
  <span class="btn">Contact Us Today</span>
</section>

<section class="programs">
  <h2>Our programs also provide students the opportunity to:</h2>
  <div class="programs-photo" role="img" aria-label="Student practising at an upright piano"></div>
  <div class="program-grid">
    <div class="program-item">Participate in large scale performances</div>
    <div class="program-item">Perform at Linden's many community events on a regular basis</div>
    <div class="program-item">Access the studio's seasonal recital stage</div>
    <div class="program-item">Attend Clinics, Masterclasses, and Jam Nights</div>
    <div class="program-item">Access the Linden Piano Band programs and ensembles</div>
    <div class="program-item">Register in our elite teaching program to learn how to pass on the magic</div>
  </div>
</section>

<section class="quote">
  <p>“Life is like a piano. What you get out of it depends on how you play it.”</p>
  <div class="q-rule"></div>
  <cite>THEO LARKIN</cite>
</section>

<section class="franchise">
  <h2>Franchise Opportunities</h2>
  <h3>BE PART OF THE LINDEN CONSERVATORY FAMILY</h3>
  <span class="btn">Shop Now</span>
</section>

<footer class="footer">
  <div class="contact">
    <div class="contact-icon">
      <svg width="18" height="18" viewBox="0 0 24 24" fill="none" stroke="#fff" stroke-width="2"><path d="M5 3h4l2 5-3 2a11 11 0 0 0 6 6l2-3 5 2v4a2 2 0 0 1-2 2A17 17 0 0 1 3 5a2 2 0 0 1 2-2z"/></svg>
    </div>
    <div><small>Call Us Now</small><strong>1-800-555-0142</strong></div>
  </div>
  <div class="footer-brand">
    <strong>CHORDS BY LINDEN</strong>
    <small>48 Maple Row, Suite 2,<br>Ashford</small>
  </div>
  <div class="contact">
    <div class="contact-icon">
      <svg width="18" height="18" viewBox="0 0 24 24" fill="none" stroke="#fff" stroke-width="2"><rect x="3" y="5" width="18" height="14"/><path d="M3 6l9 7 9-7"/></svg>
    </div>
    <div><small>Email Us</small><strong>hello@lindenmusic.example</strong></div>
  </div>
  <div class="footer-social"><span></span><span></span><span></span><span></span></div>
</footer>
<div class="legal">Copyright © 2024 Chords by Linden. All Rights Reserved.</div>

</body>
</html>
```